Infoblatt
Zielgruppe
Talentförderung, Personalentwicklung, Beratung von Personalabteilungen
Zielgruppe: Personaler, HR Verantwortliche
Aufgabenstellung
Es geht um einen "One-Pager", der auf einem Kongress ausgelegt werden soll und in Kurzform einen Überblick über unser Unternehmen und unser Angebot informieren soll.
Wir haben Visitenkarten auf Recyclingpapier und möchten das Blatt konsistent auf das gleiche Papier drucken lassen, daher einfarbig schwarz. Format DIN A4 Hoch.
IDEE: Vom Stil wie eine Infografik aufbauen
TYPO: unser LOGO ist BEBAS NEUE und unsere Schrift Helvetica

```html
<!DOCTYPE html>
<html lang="de">
<head>
<meta charset="utf-8">
<title>Sinnhalle – Infoblatt</title>
<link href="https://fonts.googleapis.com/css2?family=Bebas+Neue&family=Roboto+Condensed:wght@400;700&family=Roboto:wght@400&display=swap" rel="stylesheet">
<style>
  :root {
    --backdrop: #3a3a3a;
    --paper: #ffffff;
    --column: #bbbcc0;
    --ink: #1a1718;
    --muted: #9a9a9a;
    --highlight: #ffffff;
  }
  * { box-sizing: border-box; margin: 0; padding: 0; }
  html, body {
    width: 892px; height: 1200px; overflow: hidden;
    background: var(--backdrop);
  }
  .sheet {
    position: absolute; left: 28px; top: 0;
    width: 835px; height: 1200px;
    background: var(--paper);
    overflow: hidden;
    color: var(--ink);
    font-family: "Roboto Condensed", "Helvetica Neue", Arial, sans-serif;
  }
  .side-column {
    position: absolute; left: 505px; top: 0;
    width: 330px; height: 1200px;
    background: var(--column);
  }
  .gear-art {
    position: absolute; left: 346px; top: 120px;
    width: 433px; height: 582px;
    background: radial-gradient(ellipse at 55% 50%, rgba(255,255,255,0.55) 0%, rgba(235,235,237,0.5) 45%, rgba(220,221,224,0) 72%);
  }
  .site-url {
    position: absolute; left: 33px; top: 32px;
    font-family: "Roboto", Arial, sans-serif;
    font-size: 14px; color: var(--muted);
  }
  .brand-name {
    position: absolute; left: 31px; top: 62px;
    font-family: "Bebas Neue", "Roboto Condensed", sans-serif;
    font-size: 100px; font-weight: 400; line-height: 1;
    letter-spacing: 0.5px;
  }
  .section-title {
    position: absolute;
    font-size: 33px; font-weight: 700; line-height: 1;
  }
  .mission-title { left: 33px; top: 227px; }
  .credo-title { right: 366px; top: 458px; }
  .mission-text {
    position: absolute; left: 33px; top: 286px;
    font-size: 17.5px; line-height: 23.7px;
  }
  .mission-text span {
    display: block; text-align: justify; text-align-last: justify;
  }
  .mission-text span.last { text-align-last: left; }
  .credo-text {
    position: absolute; right: 366px; top: 510px;
    font-size: 17.5px; line-height: 23.7px; text-align: right;
    white-space: nowrap;
  }
  .team-photo {
    position: absolute; left: 0; top: 751px;
    width: 505px; height: 449px;
    background: linear-gradient(180deg, #f4f4f4 0%, #d8d8d8 35%, #8e8e8e 70%, #6f6f6f 100%);
  }
  .value-title {
    position: absolute; left: 529px; top: 771px;
    font-size: 33px; font-weight: 700; line-height: 1;
  }
  .value-title .accent { color: var(--highlight); }
  .value-text {
    position: absolute; left: 529px; top: 829px;
    font-size: 15.5px; line-height: 20.2px;
    white-space: nowrap;
  }
  .value-text p { margin-bottom: 20.2px; }
  .value-text ul { list-style: none; margin-bottom: 20.2px; }
  .value-text li { position: relative; padding-left: 23px; }
  .value-text li::before {
    content: ""; position: absolute; left: 2px; top: 7px;
    width: 7px; height: 7px; border-radius: 50%; background: var(--ink);
  }
</style>
</head>
<body>
<main class="sheet">
  <div class="side-column"></div>
  <div class="gear-art" role="img" aria-label="Großes hellgraues 3D-Zahnrad als Hintergrundmotiv"></div>

  <div class="site-url">www.sinnhalle.de</div>
  <h1 class="brand-name">SINNHALLE</h1>

  <h2 class="section-title mission-title">Mission</h2>
  <div class="mission-text">
    <span style="width:439px">Kundare heißt marktschreierisch anpreisen, hinters Licht</span>
    <span style="width:375px">führen, täuschen. Mandare heißt beauftragen,</span>
    <span style="width:326px">Vertrauen schenken. Wir legen großen Wert</span>
    <span style="width:285px">auf eine Beziehung, die Mandare, nicht</span>
    <span style="width:249px">Kundare entspricht. Für uns ist der</span>
    <span style="width:213px">partnerschaftliche Umgang</span>
    <span style="width:182px">mit unseren Mandanten</span>
    <span style="width:157px">das Fundament.</span>
    <span style="width:138px">Wir haben keine</span>
    <span style="width:120px">Kunden. Wir</span>
    <span style="width:106px">unterstützen</span>
    <span class="last">Mandanten.</span>
  </div>

  <h2 class="section-title credo-title">Credo</h2>
  <div class="credo-text">
    Wir glauben,<br>
    dass sich persönliche und<br>
    ökonomische Werte ergänzen<br>
    - mehr noch, dass sie langfristig<br>
    nicht ohne einander auskommen<br>
    und dass sich emotionale Bindung als<br>
    Mehrwert in Zahlen ausdrückt.
  </div>

  <div class="team-photo" role="img" aria-label="Schwarzweißfoto einer Gruppe von Menschen in Bewegung bei einer Besprechung"></div>

  <h2 class="value-title">Mehr<span class="accent">wert</span></h2>
  <div class="value-text">
    <p>Wir beraten Unternehmen im Rahmen der<br>Talentförderung und helfen Jugendlichen<br>auf dem Weg in ihr Berufsleben.</p>
    <p>Für Unternehmen:</p>
    <ul>
      <li>Talentförderung &amp; Talent Management</li>
      <li>Professionalisierung der Personalarbeit</li>
      <li>Organisationsentwicklung</li>
      <li>Potentialorientierte Mitarbeiterführung</li>
    </ul>
    <p>Für die junge Generation:</p>
    <ul>
      <li>Berufsorientierung</li>
      <li>Bewerbungscoaching</li>
    </ul>
  </div>
</main>
</body>
</html>
```